Upgrade website from just a link tree to a full adult content site with payment gateway.

I would like to upgrade my website VelvetKestrel.com and turn it into a pay site with a payment gateway to my content. I would like to use Wordpress. The designer needs to produce a front page with membership sign up link, payment gateway which would then provide access to the content page. We would need to be able to then go in and edit (if necessary) and load all of the content. We would like this to be as easy as possible and already have paid for a Wordpress license. We could simply allow access to our hostnimbo/Wordpress account so you can build it once all the details are confirmed. Needs to be simple to upload and have a format all set to go where we would just log in and do it. May need directions or a tutorial to get us started on the path. We are open to suggestions and ideas. We will be providing adult content. Four pages I believe. Front page , gateway video content page and picture content page. The video and picture content goes really just need to be a layout and then we can drop the videos and images in there. You can ask any other relevant questions and we can update the brief. Sorry we are fairly new to this so this is why we are looking to professionals to lead the way. Please look at current webpage for an idea of how we like the current format. It can be replicated or it can be changed. We will market and funnel our online and SoCial accounts to this page on hopes people sign up and pay membership for access to the content past the first page. Check VelvetKestrel.com for an idea of how we want to move forward. Someone goes to page. We would like to see: They can click on member log in if they have already signed up or click join and go to the payment gateway page where they can choose their membership. Once they are paid they produce their log in and lassoed. Sign in and have access to the content pages. One page can be for photos and one page can be for videos. Would consider a live stream if possible but not mandatory. Basically we want to provide content people can view for a fee. A water mark would also be nice to protect our images and video. Also if there is a way to not allow the content to be downloaded. But a water mark would protect that.

Target Market(s)

Adult entertainment

Industry/Entity Type

Adult entertainment

Coding

Coded - Design and coding required

Number of Pages Required

4 page

Font styles to use
Decorative
Script

Colors
E54698
E96AAD
F1A4CE
F9D9EA
FCEFF6
A7469A
B969AE
D3A5CF
EDDBEB
F8F0F9

Requirements
Must have
• Front page. Gateway Payment/membership sign up. Video content page set up and image content page set up. Water mark we can put on content.
Nice to have
• Live video feed capabilities. Watermark.
Should not have
• Free access to the content.

```html
<!DOCTYPE html>
<html lang="en">
<head>
<meta charset="utf-8">
<title>VelvetKestrel – Login</title>
<link rel="stylesheet" href="https://fonts.googleapis.com/css2?family=Montserrat:wght@400;500;600&family=Sofia&display=swap">
<style>
  :root {
    --pink: #eaa3c9;
    --pink-line: #e89ec6;
    --pink-text: #f1a4ce;
    --white: #ffffff;
    --black: #000000;
    --link-blue: #5a4fe6;
    --hero-dark: #1b1b1b;
    --hero-mid: #2e2e2e;
    --hero-light: #4a4a4a;
  }
  * { margin: 0; padding: 0; box-sizing: border-box; }
  html, body { width: 1200px; height: 890px; overflow: hidden; }
  body {
    position: relative;
    background: var(--black);
    font-family: "Montserrat", Arial, sans-serif;
    color: var(--white);
  }
  .hero-photo {
    position: absolute; left: 0; top: 0; width: 1200px; height: 798px;
    background:
      radial-gradient(ellipse 380px 260px at 560px 300px, var(--hero-light), transparent 70%),
      radial-gradient(ellipse 500px 300px at 1000px 120px, var(--hero-mid), transparent 75%),
      linear-gradient(160deg, var(--hero-mid) 0%, var(--hero-dark) 55%, var(--hero-mid) 100%);
  }
  .brand {
    position: absolute; left: 58px; top: 56px;
    font-size: 30px; font-weight: 500; color: var(--white);
    letter-spacing: 0.5px;
  }
  .contact-email {
    position: absolute; left: 912px; top: 24px;
    display: flex; align-items: center; gap: 10px;
    font-size: 13px; color: var(--white);
  }
  .main-nav {
    position: absolute; top: 57px; left: 0; width: 1200px; height: 26px;
  }
  .main-nav a {
    position: absolute; top: 1px;
    font-size: 17.5px; color: var(--white); text-decoration: none;
  }
  .main-nav .nav-home { left: 590px; }
  .main-nav .nav-membership { left: 688px; }
  .main-nav .nav-videos { left: 838px; }
  .main-nav .nav-gallery { left: 941px; }
  .main-nav .nav-login {
    left: 1044px; top: 0; width: 57px; height: 25px;
    background: var(--pink); border-radius: 3px;
    font-size: 12.5px; line-height: 25px; text-align: center;
  }
  .login-title {
    position: absolute; left: 0; top: 150px; width: 1200px;
    text-align: center;
    font-family: "Sofia", cursive; font-size: 60px; color: var(--pink-text);
  }
  .login-form { position: absolute; left: 456px; top: 309px; width: 289px; }
  .field {
    position: relative; width: 289px; height: 40px;
    border: 1.5px solid var(--pink-line);
    margin-bottom: 24px;
  }
  .field label {
    position: absolute; top: -6px; left: 40px;
    padding: 0 12px; font-size: 8.5px; line-height: 10px;
    color: var(--pink-text); background: #262626;
  }
  .field.password label { left: 36px; }
  .field input {
    width: 100%; height: 100%; background: transparent; border: none;
    outline: none; color: var(--white); padding: 0 12px; font: inherit;
  }
  .login-button {
    display: block; width: 289px; height: 40px; margin-top: -6px;
    background: var(--pink); border: none; border-radius: 20px;
    color: var(--white); font-family: inherit; font-size: 12px; letter-spacing: 0.3px;
  }
  .alt-login {
    position: absolute; left: 0; top: 492px; width: 1200px; text-align: center;
    font-size: 13px;
  }
  .alt-providers {
    position: absolute; left: 0; top: 524px; width: 1200px;
    display: flex; justify-content: center; gap: 18px;
  }
  .provider {
    display: flex; align-items: center; gap: 6px;
    font-size: 12px; color: var(--white); text-decoration: none;
  }
  .provider-dot { width: 14px; height: 14px; border-radius: 50%; background: var(--pink); }
  .create-account {
    position: absolute; left: 0; top: 568px; width: 1200px; text-align: center;
    font-size: 13px; color: var(--link-blue); text-decoration: none;
  }
  .site-footer {
    position: absolute; left: 0; top: 798px; width: 1200px; height: 92px;
    background: var(--black); border-top: 1px solid var(--white);
    text-align: center; font-size: 17px; line-height: 90px;
  }
  .site-footer a { color: var(--white); text-decoration: none; font-weight: 600; }
</style>
</head>
<body>
  <div class="hero-photo" role="img" aria-label="Dim black-and-white boudoir photograph of a bedroom scene"></div>

  <header>
    <div class="brand">VelvetKestrel</div>
    <div class="contact-email">
      <svg width="17" height="13" viewBox="0 0 17 13" aria-hidden="true">
        <rect x="0.5" y="0.5" width="16" height="12" fill="none" stroke="#fff" stroke-width="1"/>
        <path d="M0.5 0.5 L8.5 7 L16.5 0.5 M0.5 12.5 L6.5 6 M16.5 12.5 L10.5 6" fill="none" stroke="#fff" stroke-width="1"/>
      </svg>
      <span>velvetkestrelxxx@mailbox.com</span>
    </div>
    <nav class="main-nav">
      <a class="nav-home" href="#">Home</a>
      <a class="nav-membership" href="#">Membership</a>
      <a class="nav-videos" href="#">Videos</a>
      <a class="nav-gallery" href="#">Gallery</a>
      <a class="nav-login" href="#">Login</a>
    </nav>
  </header>

  <main>
    <h1 class="login-title">Login</h1>
    <form class="login-form">
      <div class="field email">
        <label for="email">Enter your email</label>
        <input id="email" type="email">
      </div>
      <div class="field password">
        <label for="password">Enter your password</label>
        <input id="password" type="password">
      </div>
      <button class="login-button" type="submit">LOGIN</button>
    </form>
    <p class="alt-login">Or login with:</p>
    <div class="alt-providers">
      <a class="provider" href="#"><span class="provider-dot"></span>Gloop</a>
      <a class="provider" href="#"><span class="provider-dot"></span>Friendbook</a>
    </div>
    <a class="create-account" href="#">Create an account?</a>
  </main>

  <footer class="site-footer">
    Copyright © 2020-2021 VelvetKestrel | <a href="#">Privacy</a> | <a href="#">Terms</a>
  </footer>
</body>
</html>
```